Business Card for Coastal Tundrabridge Advisory

We need a business card for Coastal Tundrabridge Advisory. The company website address is provided below. The company logo is attached. We provide specialized permafrost services to the mining, transportation, and oil & gas industries. The card should be prepared for:
Matthias Korhonen, PhD.
Coastal Tundrabridge Advisory
PO Box 418259
Quillwater, Alaska 99642
Direct: +1-907-555-0143
Email: mkorhonen@tundrabridgeadvisory.example
Website: www.coastaltundrabridgeadvisory.example

```html
<!DOCTYPE html>
<html lang="en">
<head>
<meta charset="utf-8">
<title>Coastal Tundrabridge Advisory – Business Card</title>
<link rel="stylesheet" href="https://fonts.googleapis.com/css2?family=Montserrat:wght@400;500;700&display=swap">
<style>
  :root {
    --backdrop: #9b9b9b;
    --paper: #ffffff;
    --ink: #121a24;
    --night: #121821;
    --night-mark: #232e3d;
  }
  * { box-sizing: border-box; margin: 0; padding: 0; }
  html, body { width: 1093px; height: 1200px; overflow: hidden; }
  body {
    background: var(--backdrop);
    font-family: "Montserrat", Arial, sans-serif;
    color: var(--ink);
    position: relative;
  }
  .card {
    position: absolute;
    left: 264px;
    width: 581px;
    height: 364px;
  }
  .card-front { top: 225px; background: var(--paper); }
  .card-back { top: 616px; background: var(--night); display: flex; align-items: center; justify-content: center; }

  .holder { position: absolute; left: 20px; top: 40px; }
  .holder-name { font-size: 19.5px; font-weight: 700; letter-spacing: 0.1px; }
  .holder-title { font-size: 13px; font-weight: 500; margin-top: 1px; }

  .company-name {
    position: absolute;
    right: 26px;
    top: 46px;
    text-align: right;
    font-size: 13px;
    font-weight: 700;
    line-height: 1.25;
    text-transform: uppercase;
    letter-spacing: 1.2px;
    color: var(--ink);
  }

  .contact-list { position: absolute; left: 20px; top: 257px; list-style: none; }
  .contact-item { display: flex; align-items: center; height: 25px; font-size: 13px; font-weight: 500; }
  .contact-icon { width: 14px; height: 14px; margin-right: 10px; fill: var(--ink); }

  .address {
    position: absolute;
    left: 387px;
    top: 296px;
    font-size: 13px;
    font-weight: 400;
    line-height: 1.25;
    font-style: normal;
  }

  .back-name {
    color: var(--night-mark);
    font-size: 30px;
    font-weight: 700;
    text-transform: uppercase;
    letter-spacing: 3px;
    text-align: center;
    line-height: 1.2;
  }
</style>
</head>
<body>
  <section class="card card-front" aria-label="Business card front">
    <div class="holder">
      <h1 class="holder-name">Matthias Korhonen, PhD.</h1>
      <p class="holder-title">Managing Director</p>
    </div>

    <p class="company-name">Coastal Tundrabridge<br>Advisory</p>

    <ul class="contact-list">
      <li class="contact-item">
        <svg class="contact-icon" viewBox="0 0 24 24" aria-hidden="true"><path d="M6.6 10.8a15.1 15.1 0 0 0 6.6 6.6l2.2-2.2c.3-.3.7-.4 1-.2 1.1.4 2.3.6 3.6.6.6 0 1 .4 1 1V20c0 .6-.4 1-1 1A17 17 0 0 1 3 4c0-.6.4-1 1-1h3.5c.6 0 1 .4 1 1 0 1.3.2 2.5.6 3.6.1.3 0 .7-.2 1z"/></svg>
        <span>+1-907-555-0143</span>
      </li>
      <li class="contact-item">
        <svg class="contact-icon" viewBox="0 0 24 24" aria-hidden="true"><path d="M2 5h20v2l-10 6L2 7z M2 9l10 6 10-6v10H2z"/></svg>
        <span>mkorhonen@tundrabridgeadvisory.example</span>
      </li>
      <li class="contact-item">
        <svg class="contact-icon" viewBox="0 0 24 24" aria-hidden="true"><circle cx="12" cy="12" r="10"/><path d="M7 7c2 0 3 1 3 3s-2 2-2 4-2 2-3 1M15 5c-1 2 1 3 2 4s1 3 3 3" stroke="#fff" stroke-width="1.6" fill="none"/></svg>
        <span>www.coastaltundrabridgeadvisory.example</span>
      </li>
    </ul>

    <address class="address">PO Box 418259<br>Quillwater, Alaska 99642</address>
  </section>

  <section class="card card-back" aria-label="Business card back">
    <p class="back-name">Coastal Tundrabridge<br>Advisory</p>
  </section>
</body>
</html>
```